Cruise Booking Website

Cruise search and booking website

This project is a redesign of a cruise booking website we did a few years ago.

The current website is located here: http://voyage.pylonworks.example/en/

It's not fully functional but gives you ad idea how miserable the old design was.

All the information about cruises, cruise lines, destinations, ports and shore excursions will be similar to http://www.sailquest.example/
Actual search pages (form, results, single result, sailing and cabin selection, ship info, booking) will have EXACTLY the same info as sailquest.example

We like the style of http://harborfleetdesk.example, it's quite modern, good spacing, not overloaded with information. So you can use it as an example of what we like, not what we want as a final result for us. Please, don't copy it. The result should not be possible to resemble the harborfleetdesk.example, because our site has to be unique. This is important!
If you submit a design that clearly reminds another cruise site it will be rejected!

Also the mockup provided is just to give you the basic structure and show what information has to be present on the page. It doesn't mean the layout has to be the same as a mockup. The layout is up to the designer.

I've updated the mockup to be more generic so it doesn't confuse you:
https://files.boxvault.example/s/k7m2qp9wz4hx/Home%20page.png

When you're adding social sharing icons like plazanet/chirpline you have to use chinese ones instead:
https://files.boxvault.example/s/t3nr8vx5lc2e/chinese-social-icons.png
Originals: http://minilk.example/qR7t

We'll start with home page first and after it's approved inner pages can be designed.

I know the cost of the project doesn't look high, but the task is straight forward and doesn't require to be very original, it's better to follow existing design and layout patterns that proved to work well.
That's why I encourage you to choose a template to build the design on top of one of https://themeparlor.example/ themes if it will save the design work, will be easier and faster for you. So it will be more like a customization than a new design from scratch.

Mockups, site map and logo files:
- https://files.boxvault.example/sh/h48dm2rs73fkpw/QvnbW2Xz8e

Website tree:
- https://sheets.papernest.example/document/d/7xPqR2mLw9sTk4VbN8cHj3YzA6eUf5GdKo1iMnBv/edit?usp=sharing
Updates

So far a lot of designs are just copying http://www.harborfleetdesk.example/ - we don't like it!

We like the style of harborfleetdesk.example, it's quite modern, good spacing, not overloaded with information. So you can use it as an example of what we like, not what we want as a final result for us. Please, don't copy it. The result should not be possible to resemble the harborfleetdesk.example, because our site has to be unique. This is important!

Target Market(s)

Chinese travellers

Industry/Entity Type

Build

Requirements
Must have
• * White, blue and red
* Large spacing, not too much information cramped into a small space like sailquest.example or the current website
* More "hidden" info in popups, tabs and so on, so not to many things are visible at the same time
* Compatible with kestrel scaffold styling (for easier coding):
- http://kestrelkit.codeshelf.example/scaffold/index.html
- http://skinmarket.example/
* Feel free to propose to build the design on top of one of https://themeparlor.example/ themes if it will save the design work, will be easier and faster for you

```html
<!DOCTYPE html>
<html lang="en">
<head>
<meta charset="utf-8">
<title>Bluewake – Cruise Booking</title>
<link href="https://fonts.googleapis.com/css2?family=PT+Sans:wght@400;700&family=PT+Sans+Narrow:wght@400;700&display=swap" rel="stylesheet">
<style>
:root{
  --blue:#1a6fb5;
  --blue-dark:#0f4f8c;
  --blue-nav:#1478c8;
  --blue-light:#2a93dd;
  --panel:#2a7cbd;
  --panel-border:#1c5f99;
  --orange:#f7931e;
  --orange-dark:#e8700c;
  --orange-text:#e8660c;
  --text:#333;
  --muted:#666;
  --line:#d9d9d9;
  --row:#f0f0f0;
  --footer:#3f6e9f;
  --footer-bottom:#35628f;
  --white:#fff;
}
*{box-sizing:border-box;margin:0;padding:0}
html,body{width:1167px;height:1200px;overflow:hidden}
body{font-family:"PT Sans",sans-serif;color:var(--text);background:#2f6ba6}
.page{position:relative;width:1400px;height:1440px;transform:scale(0.83357);transform-origin:0 0;
  background:radial-gradient(ellipse 60% 55% at 50% 40%,#e8f2fb 0%,#9cc5ea 40%,#3f86c7 75%,#2b69a8 100%)}
.abs{position:absolute}
.sheet{left:210px;top:0;width:980px;height:1168px;background:var(--white)}

/* header */
.brand{left:224px;top:40px;display:flex;align-items:center;gap:10px}
.brand-mark{width:56px;height:56px;border-radius:50%;background:var(--blue)}
.brand-name{font-size:42px;font-weight:700;color:var(--blue);line-height:1}
.brand-url{position:absolute;left:66px;top:46px;font-size:11px;font-weight:700;color:var(--blue);letter-spacing:.5px;white-space:nowrap}
.account{left:927px;top:20px;font-size:13px;color:var(--blue)}
.account span{margin:0 10px}
.socials{left:1054px;top:16px;display:flex;gap:6px}
.socials i{display:block;width:26px;height:26px;border-radius:4px}
.phone{left:740px;top:56px;display:flex;gap:10px;align-items:center}
.phone-icon{width:36px;height:36px;border-radius:50%;border:2px solid #999;display:flex;align-items:center;justify-content:center}
.phone-num{font-size:23px;font-weight:700;color:var(--blue);line-height:1}
.phone-cta{font-size:18px;color:#222}
.search{left:940px;top:76px;width:230px;height:26px;border:1px solid #ccc;border-radius:3px;font-size:10px;color:#888;padding:6px 10px;background:#fafafa}
.search svg{position:absolute;right:8px;top:5px}

/* nav */
.nav{left:210px;top:130px;width:980px;height:40px;background:linear-gradient(#1a84d2,#0f5ea8);display:flex}
.nav a{color:#fff;font-family:"PT Sans Narrow",sans-serif;font-weight:700;font-size:13px;text-decoration:none;display:flex;align-items:center;justify-content:center;border-right:1px solid rgba(255,255,255,.15)}
.nav a.active{background:linear-gradient(#29a3e8,#1884d0)}

/* side panels */
.panel{background:var(--panel);border:1px solid var(--panel-border);color:#fff;border-radius:2px}
.finder{left:232px;top:193px;width:288px;height:407px}
.finder h2{position:absolute;left:25px;top:18px;font-weight:400;font-size:26px}
.finder .rule{position:absolute;left:4px;right:4px;top:55px;border-top:1px solid rgba(255,255,255,.3)}
.lbl{position:absolute;font-size:14px;color:#e3efff}
.sel{position:absolute;height:27px;background:linear-gradient(#f2f2f2,#d8d8d8);border-radius:2px;color:#222;font-size:11px;padding:7px 10px}
.sel::after{content:"";position:absolute;right:0;top:0;width:22px;height:27px;border-left:1px solid #bbb}
.sel b{position:absolute;right:7px;top:6px;font-size:8px;color:#777;line-height:7px;font-weight:400;z-index:1}
.check{position:absolute;left:23px;top:320px;font-size:11px;color:#dbe8f7;display:flex;gap:4px;align-items:center}
.check i{width:13px;height:13px;background:#e9e9e9;display:block}
.btn-search{position:absolute;left:22px;top:346px;width:245px;height:39px;background:linear-gradient(#fda435,#f07d10);border-radius:2px;font-size:18px;font-weight:700;color:#fff;text-align:center;line-height:39px}

.news{left:232px;top:626px;width:288px;height:346px}
.news-photo{position:absolute;left:13px;top:16px;width:262px;height:155px;background:#fff;padding:6px}
.news-photo div{width:100%;height:100%;background:linear-gradient(135deg,#4fb8e0 0%,#78c9e8 40%,#e8d2b8 70%,#3d7fbf 100%)}
.news h3{position:absolute;left:23px;top:184px;font-size:15px}
.news p{position:absolute;left:23px;top:211px;font-size:11px}
.news .email{position:absolute;left:23px;top:238px;width:250px;height:26px;background:#fff;border-radius:2px;font-size:11px;color:#888;padding:6px 12px}
.news .sub{position:absolute;left:24px;top:278px;width:102px;height:26px;background:#0c3c6c;border-radius:2px;font-size:12px;text-align:center;line-height:26px}
.news .rules{position:absolute;left:26px;top:313px;font-size:12px}

/* main */
.crumb{left:554px;top:193px;font-size:12px;color:var(--blue)}
.crumb span{color:#999;margin:0 6px}
.frame{border:1px solid var(--line);background:#fff;padding:7px}
.ship-photo{left:550px;top:230px;width:216px;height:156px}
.ship-photo div,.map div{width:100%;height:100%}
.ship-photo div{background:linear-gradient(#6f9ad2 0%,#a9c5e8 45%,#1d5fa8 60%,#0d3f7c 100%)}
.map{left:550px;top:433px;width:216px;height:156px}
.map div{background:linear-gradient(150deg,#bcd7f2 0%,#e9eee4 30%,#eef0ea 100%)}
.cruise-title{left:783px;top:230px;font-size:14px;font-weight:700;color:var(--blue)}
.cruise-line{left:783px;top:257px;font-size:11px;color:#111}
.cruise-route{left:783px;top:279px;font-size:11px;color:#222}
.cruise-route a{color:var(--blue);text-decoration:none}
.prices{left:783px;top:308px;display:flex;gap:5px}
.price{width:92px;height:56px;border:1px solid var(--line);font-size:10px;color:#555;text-align:center;padding-top:8px;line-height:13px}
.price b{font-weight:400;color:var(--blue);display:block}
.btn-select-dark{left:1097px;top:378px;width:70px;height:22px;background:linear-gradient(#1c6fc0,#0e4d8e);color:#fff;font-size:9px;text-align:center;line-height:22px;border-radius:2px}
.divider{left:550px;top:413px;width:617px;border-top:1px solid var(--line)}

.day{left:786px;width:382px;height:44px;border:1px solid var(--line);background:linear-gradient(#fff,#f4f4f4);font-size:10px;color:var(--blue);font-weight:700}
.day .tag{position:absolute;left:5px;top:6px;width:56px;height:32px;background:linear-gradient(#fca033,#ee790c);color:#fff;text-align:center;line-height:32px;border-radius:2px}
.day span{position:absolute}
.day .or{color:var(--orange-text)}

.tabs{left:548px;top:650px;display:flex;gap:1px}
.tab{height:36px;font-size:10px;color:#fff;display:flex;align-items:center;justify-content:center;background:linear-gradient(#fda435,#f18313)}
.tab.active{background:linear-gradient(#1b78c4,#0f5597)}
.tab-body{left:548px;top:686px;width:620px;height:322px;border:1px solid var(--line)}
.sail-head{position:absolute;left:20px;top:21px;width:580px;height:34px;background:var(--blue-nav);color:#fff;font-size:10px;font-weight:700}
.sail-head span,.sail-row span{position:absolute;top:0}
.sail-row{position:absolute;left:20px;width:580px;height:35px;font-size:10px;color:#555;line-height:35px}
.sail-row:nth-child(even){background:var(--row)}
.sail-row .date{color:var(--blue);font-weight:700}
.sail-row .go{left:482px;top:7px;width:90px;height:20px;background:linear-gradient(#fda435,#ef7a0d);color:#fff;font-weight:700;text-align:center;line-height:20px;border-radius:2px}
.more{position:absolute;left:26px;top:282px;font-size:13px;color:var(--orange-text);text-decoration:underline;font-style:italic}

/* partners */
.partners-title{left:228px;top:1034px;font-size:18px;font-weight:700;color:var(--blue)}
.arrows{left:1127px;top:1035px;display:flex;gap:4px}
.arrows i{width:20px;height:20px;background:#e4e4e4;border:1px solid #ccc;display:flex;align-items:center;justify-content:center}
.partner{top:1070px;width:145px;height:72px;border:1px solid #d4d4d4;display:flex;align-items:center;justify-content:center;font-size:18px;font-weight:700;color:var(--blue)}

/* footer */
.footer{left:210px;top:1168px;width:980px;height:222px;background:var(--footer);color:#fff}
.footer-bottom{left:210px;top:1390px;width:980px;height:50px;background:var(--footer-bottom);color:#fff;font-size:10px;text-align:center;line-height:50px}
.fcol{position:absolute;top:30px}
.fcol h4{font-size:16px;margin-bottom:10px}
.fcol li{list-style:none;font-size:11px;line-height:22px}
.about-logo{position:absolute;left:405px;top:74px;width:100px;height:98px;background:#fff;border:1px solid #ccc;display:flex;flex-direction:column;align-items:center;justify-content:center;gap:6px;color:var(--blue);font-weight:700;font-size:13px}
.about-logo i{width:48px;height:48px;border-radius:50%;background:var(--blue);display:block}
.about-text{position:absolute;left:524px;top:80px;width:120px;font-size:12px;line-height:18px}
.contact{position:absolute;left:705px;top:72px;font-size:13px;line-height:19px}
.contact .line{display:flex;gap:8px;align-items:center;margin-top:8px;font-size:12px}
</style>
</head>
<body>
<div class="page">
  <div class="abs sheet"></div>

  <header>
    <div class="abs brand">
      <i class="brand-mark"></i>
      <span class="brand-name">Bluewake</span>
      <span class="brand-url">www.bluewake.example</span>
    </div>
    <div class="abs account">Sign in<span>|</span>Signup</div>
    <div class="abs socials" aria-label="Social links">
      <i style="background:#e0322c"></i><i style="background:#27a3de"></i><i style="background:#f29a14"></i><i style="background:#d92a2a"></i>
    </div>
    <div class="abs phone">
      <div class="phone-icon">
        <svg width="18" height="18" viewBox="0 0 24 24"><path d="M6.6 10.8a15.1 15.1 0 0 0 6.6 6.6l2.2-2.2c.3-.3.7-.4 1-.2 1.1.4 2.3.6 3.6.6.6 0 1 .4 1 1V20c0 .6-.4 1-1 1A17 17 0 0 1 3 4c0-.6.4-1 1-1h3.5c.6 0 1 .4 1 1 0 1.3.2 2.5.6 3.6.1.3 0 .7-.2 1z" fill="none" stroke="#777" stroke-width="1.6"/></svg>
      </div>
      <div><div class="phone-num">400 555 018</div><div class="phone-cta">Call Us Today!</div></div>
    </div>
    <div class="abs search">SEARCH :
      <svg width="14" height="14" viewBox="0 0 14 14"><circle cx="6" cy="6" r="4.5" fill="none" stroke="#bbb" stroke-width="1.5"/><path d="M9.3 9.3L13 13" stroke="#bbb" stroke-width="1.5"/></svg>
    </div>
  </header>

  <nav class="abs nav">
    <a class="active" style="width:101px">HOME</a>
    <a style="width:140px">DESTINATIONS</a>
    <a style="width:128px">CRUISE LINES</a>
    <a style="width:127px">CRUISE INFO</a>
    <a style="width:94px">DEALS</a>
    <a style="width:153px">ONLINE BOOKING</a>
    <a style="width:125px">CONTACT US</a>
    <a style="width:112px;border-right:0">BLOG</a>
  </nav>

  <aside class="abs panel finder">
    <h2>Find Your Cruise</h2>
    <div class="rule"></div>
    <span class="lbl" style="left:23px;top:67px">Destination</span>
    <div class="sel" style="left:23px;top:87px;width:239px">Destination name<b>▲<br>▼</b></div>
    <span class="lbl" style="left:23px;top:121px">Length</span>
    <span class="lbl" style="left:153px;top:121px">Month</span>
    <div class="sel" style="left:23px;top:141px;width:108px">Length Area</div>
    <div class="sel" style="left:153px;top:141px;width:109px"><b>▲<br>▼</b></div>
    <span class="lbl" style="left:21px;top:177px">Cruise Lines</span>
    <div class="sel" style="left:21px;top:197px;width:242px">Any Cruise line<b>▲<br>▼</b></div>
    <span class="lbl" style="left:21px;top:238px;font-size:15px">Number of Travelers</span>
    <span class="lbl" style="left:23px;top:264px">Age 25+</span>
    <span class="lbl" style="left:153px;top:264px">Age 0 to 24</span>
    <div class="sel" style="left:23px;top:284px;width:106px;background:linear-gradient(#eee,#d6d6d6)">5<b>▲<br>▼</b></div>
    <div class="sel" style="left:153px;top:284px;width:107px">0<b>▲<br>▼</b></div>
    <div class="check"><i></i>Check for senior rates</div>
    <div class="btn-search">Search Cruises</div>
  </aside>

  <aside class="abs panel news">
    <div class="news-photo"><div role="img" aria-label="Photo of a retired couple relaxing in deck chairs by a pool"></div></div>
    <h3>Cruise Deals Newsletter</h3>
    <p>Subscribe to the best Cruise deals Now!</p>
    <div class="email">Email :</div>
    <div class="sub">Subscribe</div>
    <div class="rules">Contest Rules</div>
  </aside>

  <main>
    <div class="abs crumb">HOME<span>›</span>ABOUT US</div>
    <div class="abs frame ship-photo"><div role="img" aria-label="Photo of a white cruise ship at sea"></div></div>
    <div class="abs cruise-title">3 DAYS BAHAMAS</div>
    <div class="abs cruise-line">NORTHSTAR CRUISE LINE. NORTHSTAR AURORA</div>
    <div class="abs cruise-route"><a>Miami, Great ay, Nassau, Miami</a>&nbsp;&nbsp; | &nbsp;&nbsp;4 departure dates : Sep 6, 13, 20, 27 2013</div>
    <div class="abs prices">
      <div class="price">Inside from<b>$174</b>$58 per day</div>
      <div class="price">Ocean view from<b>$174</b>$58 per day</div>
      <div class="price">Inside from<b>$174</b>$58 per day</div>
      <div class="price">Inside from<b>$174</b>$58 per day</div>
    </div>
    <div class="abs btn-select-dark">SELECT</div>
    <div class="abs divider"></div>

    <div class="abs frame map"><div role="img" aria-label="Route map near the island stop"></div></div>

    <div class="abs day" style="top:433px"><div class="tag">DAY-1</div><span style="left:71px;top:8px">THU</span><span style="left:115px;top:8px">SEP 5</span><span style="left:165px;top:8px">PORT CANAVERAL</span><span class="or" style="left:165px;top:24px">ARRIVE : 3:45PM</span><span class="or" style="left:295px;top:24px">DEPART 3:45PM</span></div>
    <div class="abs day" style="top:483px"><div class="tag">DAY-1</div><span style="left:71px;top:8px">THU</span><span style="left:115px;top:8px">SEP 5</span><span style="left:165px;top:8px">PORT CANAVERAL</span><span class="or" style="left:165px;top:24px">ARRIVE : 3:45PM</span><span class="or" style="left:295px;top:24px">DEPART 3:45PM</span></div>
    <div class="abs day" style="top:533px"><div class="tag">DAY-1</div><span style="left:71px;top:8px">THU</span><span style="left:115px;top:8px">SEP 5</span><span style="left:165px;top:8px">PORT CANAVERAL</span><span class="or" style="left:165px;top:24px">ARRIVE : 3:45PM</span><span class="or" style="left:295px;top:24px">DEPART 3:45PM</span></div>
    <div class="abs day" style="top:583px"><div class="tag">DAY-1</div><span style="left:71px;top:8px">THU</span><span style="left:115px;top:8px">SEP 5</span><span style="left:165px;top:8px">PORT CANAVERAL</span><span class="or" style="left:165px;top:24px">ARRIVE : 3:45PM</span><span class="or" style="left:295px;top:24px">DEPART 3:45PM</span></div>

    <div class="abs tabs">
      <div class="tab active" style="width:145px">SAILING</div>
      <div class="tab" style="width:135px">SHIP</div>
      <div class="tab" style="width:135px">DECKS</div>
      <div class="tab" style="width:135px">HIGHLIGHTS</div>
    </div>
    <div class="abs tab-body">
      <div class="sail-head"><span style="left:14px;top:11px">SAILINGS</span><span style="left:172px;top:11px">INSIDE OCEANVIEW BALCPNY SUITE</span></div>
      <div style="position:absolute;left:0;top:59px;width:100%">
        <div class="sail-row" style="top:0"><span class="date" style="left:14px">THU, SEP 05,13</span><span style="left:174px">$472&nbsp; $490</span><span style="left:284px">$587</span><span style="left:384px">$1575</span><span class="go">SELECT</span></div>
        <div class="sail-row" style="top:35px"><span class="date" style="left:14px">THU, SEP 05,13</span><span style="left:174px">$472&nbsp; $490</span><span style="left:284px">$587</span><span style="left:384px">$1575</span><span class="go">SELECT</span></div>
        <div class="sail-row" style="top:70px"><span class="date" style="left:14px">THU, SEP 05,13</span><span style="left:174px">$472&nbsp; $490</span><span style="left:284px">$587</span><span style="left:384px">$1575</span><span class="go">SELECT</span></div>
        <div class="sail-row" style="top:105px"><span class="date" style="left:14px">THU, SEP 05,13</span><span style="left:174px">$472&nbsp; $490</span><span style="left:284px">$587</span><span style="left:384px">$1575</span><span class="go">SELECT</span></div>
        <div class="sail-row" style="top:140px"><span class="date" style="left:14px">THU, SEP 05,13</span><span style="left:174px">$472&nbsp; $490</span><span style="left:284px">$587</span><span style="left:384px">$1575</span><span class="go">SELECT</span></div>
        <div class="sail-row" style="top:175px"><span class="date" style="left:14px">THU, SEP 05,13</span><span style="left:174px">$472&nbsp; $490</span><span style="left:284px">$587</span><span style="left:384px">$1575</span><span class="go">SELECT</span></div>
      </div>
      <div class="more">Show me more departure dates</div>
    </div>
  </main>

  <section>
    <h3 class="abs partners-title">OUR RELIABLE PARTNERS</h3>
    <div class="abs arrows">
      <i><svg width="8" height="10"><path d="M6 1L2 5l4 4" fill="none" stroke="#888" stroke-width="1.5"/></svg></i>
      <i><svg width="8" height="10"><path d="M2 1l4 4-4 4" fill="none" stroke="#888" stroke-width="1.5"/></svg></i>
    </div>
    <div class="abs partner" style="left:229px">Meridian</div>
    <div class="abs partner" style="left:389px">Solara</div>
    <div class="abs partner" style="left:549px">Azurine</div>
    <div class="abs partner" style="left:709px">Quaywise</div>
    <div class="abs partner" style="left:869px">Lagoon Mkt.</div>
    <div class="abs partner" style="left:1029px">Pier Roussin</div>
  </section>

  <footer class="abs footer">
    <div class="fcol" style="left:32px"><h4>Useful Pages</h4><ul><li>About Us</li><li>Contact us</li><li>Blog</li><li>FAQ</li><li>Terms of Service</li><li>Payment info</li><li>Reward Points</li></ul></div>
    <div class="fcol" style="left:222px"><h4>Cruise Infov</h4><ul><li>Cruise news</li><li>Visa</li><li>Honeymoon cruises</li><li>Firsttime on a Cruise</li></ul></div>
    <div class="fcol" style="left:405px;top:36px"><h4 style="font-size:15px">About bluewake.example</h4></div>
    <div class="about-logo"><i></i>Bluewake</div>
    <div class="about-text">We're the most advanced cruise booking providr in china.</div>
    <div class="fcol" style="left:705px;top:36px"><h4 style="font-size:15px">Contact Us</h4></div>
    <div class="contact">
      Halvern Studio,Pte Ltd<br>Westbay center x118, Harbor Ave 3.0<br>Lorvenna 20417 Aldovia
      <div class="line" style="margin-top:10px"><svg width="14" height="12" viewBox="0 0 14 12"><path d="M1 4c3-3 9-3 12 0l-2 2-2-1V3H5v2L3 6z" fill="#fff"/><rect x="3" y="7" width="8" height="4" fill="#fff"/></svg>(123) 555-0190 - (123)555-0142</div>
      <div class="line"><svg width="14" height="10" viewBox="0 0 14 10"><rect x="0.5" y="0.5" width="13" height="9" fill="none" stroke="#fff"/><path d="M1 1l6 5 6-5" fill="none" stroke="#fff"/></svg>email@bluewake.example</div>
    </div>
  </footer>
  <div class="abs footer-bottom">© 2013. Bluewake. All rights reserved.</div>
</div>
</body>
</html>
```